Financial Broker firm looking for Brochure design/Pdf-document

Job Type
Brochure Design/PDF-Document
Task Outline
Create a Brochure Design that also works for sending as pdf-document.
Task Description
We need a combined corporate brochure (Booklet style) to give out to potential clients as well as sending it to potential clients through Internet as pdf-document.
We need a background template with pictures and colors that gives the impression of professionalism, trustworthiness and seriousness. Attached text in English but the text will be translated into different languages to fit different markets. Therefore we would like to receive one template including the text and one without any text (but with the logo). Please inform us where (any) pictures and/or photos on the template have been taken from in order for us to buy and use them legally.
About Us
Our company Quelvo Brokerage AB is a financial brokerage company who provides a diversity of services for different selected partners (www.quelvobrokerage.example).
Target Market
Companies on all levels, domestic or international
Requirements
Must Have:
-The text and logo attached below
Industry/Entity Type
Financial
Look and feel
Each slider illustrates characteristics of the customer's brand and the style your logo design should communicate.

```html
<!DOCTYPE html>
<html lang="en">
<head>
<meta charset="UTF-8">
<title>Quelvo Brokerage AB – Brochure Cover</title>
<link rel="stylesheet" href="https://fonts.googleapis.com/css2?family=Arimo:wght@400;700&family=Roboto+Condensed:wght@400;700&display=swap">
<style>
  :root {
    --blue-deep: #0b3f86;
    --blue-mid: #1f63b4;
    --blue-light: #5b9ad8;
    --blue-pale: #cfe1f3;
    --text-blue: #1c5aa6;
    --ink: #1b1b1b;
    --rule: #b9cde4;
    --white: #ffffff;
  }
  * { margin: 0; padding: 0; box-sizing: border-box; }
  html, body { width: 809px; height: 1200px; overflow: hidden; background: var(--white); }
  .cover {
    position: relative;
    width: 809px;
    height: 1200px;
    background: var(--white);
    font-family: "Arimo", Arial, sans-serif;
    overflow: hidden;
  }
  .hero-photo {
    position: absolute;
    left: 0; top: 0;
    width: 809px; height: 560px;
    background:
      radial-gradient(ellipse at 78% 28%, rgba(255,255,255,0.35), rgba(255,255,255,0) 45%),
      linear-gradient(160deg, var(--blue-mid) 0%, var(--blue-deep) 55%, var(--blue-light) 100%);
  }
  .hero-swoosh {
    position: absolute;
    left: 0; top: 380px;
    width: 809px; height: 200px;
  }
  .tagline {
    position: absolute;
    left: 210px; top: 140px;
    color: var(--white);
    font-size: 33px;
    font-weight: 400;
    letter-spacing: 0.2px;
  }
  .services {
    position: absolute;
    right: 50px; top: 620px;
    width: 360px;
    list-style: none;
    font-family: "Roboto Condensed", "Arial Narrow", sans-serif;
  }
  .services li {
    text-align: right;
    color: var(--text-blue);
    font-size: 27px;
    line-height: 1;
    padding: 12px 0 11px;
    border-bottom: 1px solid var(--rule);
  }
  .services li:last-child { border-bottom: none; }
  .brand {
    position: absolute;
    left: 0; right: 0; top: 1000px;
    display: flex;
    justify-content: center;
    align-items: center;
    gap: 14px;
  }
  .brand-name {
    font-family: "Arimo", Arial, sans-serif;
    font-weight: 700;
    font-size: 44px;
    color: var(--ink);
    letter-spacing: 1px;
  }
  .brand-dot {
    width: 40px; height: 40px;
    border-radius: 50%;
    background: var(--blue-mid);
  }
  .footer-band {
    position: absolute;
    left: 0; bottom: 0;
    width: 809px; height: 80px;
    background: linear-gradient(90deg, var(--blue-mid), var(--blue-deep));
  }
  .footer-url {
    position: absolute;
    right: 40px; bottom: 28px;
    color: var(--white);
    font-size: 17px;
    letter-spacing: 1.5px;
    text-transform: uppercase;
  }
</style>
</head>
<body>
  <main class="cover">
    <div class="hero-photo" role="img" aria-label="Businessman in a suit pointing at a rising financial chart on a blue screen"></div>
    <svg class="hero-swoosh" viewBox="0 0 809 200" preserveAspectRatio="none" aria-hidden="true">
      <path d="M0 120 C 250 40, 520 30, 809 70 L809 200 L0 200 Z" fill="var(--blue-pale)" opacity="0.6"/>
      <path d="M0 160 C 260 90, 540 80, 809 110 L809 200 L0 200 Z" fill="var(--white)"/>
    </svg>
    <h1 class="tagline">A partner in need as in success</h1>

    <ul class="services">
      <li>Foreign exchange service</li>
      <li>Covering financial risks</li>
      <li>Trade credit insurance</li>
      <li>Bonding</li>
      <li>Trade debt collections</li>
      <li>Factoring</li>
    </ul>

    <div class="brand">
      <span class="brand-dot" aria-hidden="true"></span>
      <span class="brand-name">QUELVO BROKERAGE</span>
    </div>

    <footer class="footer-band">
      <span class="footer-url">www.quelvobrokerage.example</span>
    </footer>
  </main>
</body>
</html>
```